New Flyer Design Project

I have an Upmarket Hair and Beauty Salon near the beach. I already have a current logo but it needs to change to Hair AND Beauty as we were only doing beauty. I want it to have a special on the flyer and to be DL size. I like it to be elegant with soft colours. I like the blues/teals also. I have attached the current business cards. I want it to tie in with the business cards somehow as well. I want the add to have something along the lines of - Marnie & Tess now introduce to you Hair AND Beauty. We have combined our team to offer you all of your hair and beauty needs in the one great location! NEW CLIENTS OFFER $49 Style Cut & Blowdry and 30% off ALL Waxing

We are a Velunique and Solvadermix Salon so you can google to get the feel of the brand. The flyer will be used as a leaflet drop.
Please include an expiry of march 31st 2015
I would prefer not to use stock images also
Phone Number 08 9473 2804
shop 4&5 Corrow Point Pde
Yanchep 6035

Thankyou :)

Target Market(s)

20-40

Industry/Entity Type

Hair

Requirements
Must have
• DL size
Address & Contact details
08 9473 2804
shop 4&5 Corrow Point Pde
Seabrook 6041
Should not have
• Do not like clip arts-scissors etc
Would prefer not to use stock images

```html
<!DOCTYPE html>
<html lang="en">
<head>
<meta charset="utf-8">
<title>Marnie &amp; Tess – New Clients Offer</title>
<link href="https://fonts.googleapis.com/css2?family=Source+Sans+3:ital,wght@0,400;0,700;1,400&family=Tinos:wght@400;700&family=Roboto+Condensed:wght@500;700&display=swap" rel="stylesheet">
<style>
  :root{
    --panel:#363b48;
    --panel-light:#414857;
    --teal:#5fd6cf;
    --pink:#f27fc0;
    --white:#ffffff;
    --brown:#6b4a2c;
    --badge:#a3258e;
    --orange:#ff8a1f;
    --sans:'Source Sans 3', sans-serif;
    --serif:'Tinos', serif;
    --condensed:'Roboto Condensed', sans-serif;
  }
  *{margin:0;padding:0;box-sizing:border-box}
  html,body{width:848px;height:1200px;overflow:hidden;background:#ffffff}
  .flyer{position:relative;width:848px;height:1200px;overflow:hidden;font-family:var(--sans);color:var(--white)}
  .backdrop{position:absolute;inset:0}
  .logo-box{position:absolute;left:34px;top:27px;width:438px;height:104px;background:var(--white);border:1.5px solid var(--brown);display:flex;align-items:center;justify-content:center}
  .logo-name{font-family:var(--sans);font-weight:400;font-size:54px;line-height:1;color:var(--brown);letter-spacing:1px}
  .brand-note{position:absolute;left:39px;top:181px;width:272px;font-style:italic;font-size:30px;line-height:39px;color:var(--teal)}
  .intro{position:absolute;left:39px;top:544px;width:270px;font-size:39px;line-height:50px;color:var(--pink)}
  .team-note{position:absolute;left:39px;top:874px;width:228px;font-style:italic;font-size:21.5px;line-height:29px}
  .contact{position:absolute;left:39px;top:1066px}
  .contact-address{font-size:19px}
  .contact-phone{font-weight:700;font-size:46px;line-height:52px;letter-spacing:0.5px}
  .contact-email{font-weight:700;font-size:17.5px}
  .offer-title{position:absolute;left:424px;top:564px;width:278px;font-family:var(--serif);font-weight:700;text-align:center;line-height:1}
  .offer-kicker{font-size:30px}
  .offer-main{font-size:80px;margin-top:-8px}
  .deal{position:absolute;top:716px;font-family:var(--serif);font-weight:400}
  .deal-value{font-size:86px;line-height:80px;font-weight:700}
  .deal-desc{font-size:35px;line-height:42px;letter-spacing:0.5px}
  .deal-cut{left:355px}
  .deal-wax{left:622px}
  .expiry{position:absolute;left:568px;top:955px;width:188px;height:188px}
  .expiry-text{position:absolute;inset:0;display:flex;flex-direction:column;align-items:center;justify-content:center;font-family:var(--condensed);font-weight:500;font-size:25px;line-height:27px;text-align:center}
  .expiry-year{font-weight:700;font-size:38px;line-height:40px;color:var(--orange)}
</style>
</head>
<body>
<div class="flyer">
  <svg class="backdrop" width="848" height="1200" viewBox="0 0 848 1200">
    <defs>
      <linearGradient id="photoTones" x1="0" y1="0" x2="0.3" y2="1">
        <stop offset="0" stop-color="#f7e8d6"/>
        <stop offset="0.35" stop-color="#f1c9a8"/>
        <stop offset="0.58" stop-color="#de6fae"/>
        <stop offset="0.8" stop-color="#9d5cb8"/>
        <stop offset="1" stop-color="#5d8fd8"/>
      </linearGradient>
    </defs>
    <rect width="848" height="1200" fill="url(#photoTones)" role="img" aria-label="Beauty portrait photograph with soft lily and pastel bokeh light"/>
    <polygon points="0,0 450,0 303,469 524,1200 0,1200" fill="var(--panel)"/>
    <polygon points="0,0 410,0 275,469 470,1200 0,1200" fill="var(--panel-light)" opacity="0.45"/>
    <polygon points="0,0 330,0 0,1200" fill="var(--panel)" opacity="0.35"/>
  </svg>

  <div class="logo-box">
    <div class="logo-name">Marnie &amp; Tess</div>
  </div>

  <p class="brand-note">We are a Velunique and Solvadermix Salon so you can google to get the feel of the brand</p>
  <p class="intro">WE introduce to you Hair care &amp; Beauty</p>
  <p class="team-note">We have combined our team to offer you all of your hair and beauty needs in the one great location</p>

  <div class="contact">
    <div class="contact-address">shop 4&amp;5 Corrow Point Pde Seabrook 6041</div>
    <div class="contact-phone">08 9473 2804</div>
    <div class="contact-email">marnie.tess.beauty@postmail.net</div>
  </div>

  <div class="offer-title">
    <div class="offer-kicker">NEW CLIENTS</div>
    <div class="offer-main">OFFER</div>
  </div>

  <div class="deal deal-cut">
    <div class="deal-value">$49</div>
    <div class="deal-desc">STYLE CUT<br>&amp; BLOWDRY</div>
  </div>
  <div class="deal deal-wax">
    <div class="deal-value">30%</div>
    <div class="deal-desc">OFF ALL<br>WAXING</div>
  </div>

  <div class="expiry">
    <svg width="188" height="188" viewBox="0 0 188 188">
      <circle cx="94" cy="94" r="90" fill="var(--badge)"/>
      <circle cx="94" cy="94" r="85" fill="none" stroke="var(--white)" stroke-width="3" stroke-dasharray="6 4"/>
    </svg>
    <div class="expiry-text">
      <span>EXPIRY OF</span>
      <span>MARCH</span>
      <span>31ST</span>
      <span class="expiry-year">2015</span>
    </div>
  </div>
</div>
</body>
</html>
```